Business card for law firm

Need business card for new law firm. Think confident, authoritative, conservative, but not stuffy or old-fashioned.

Contact Information for Business Card

Content for card - logo (uploaded), plus the following:

Paul Whitcombe (larger font)
Managing Partner (larger font, but not as large as name)
Level 9, 7 Ferris Lane
Sydney NSW 2000
Main Tel 02 9364 2710
Direct Tel 02 8472 3159
Email paul@qvlegal.com.au
www.qvlegal.com.au

Letterhead design should include logo plus:
Level 9, 7 Ferris Lane
Sydney NSW 2000
Tel 02 8472 3159
www.qvlegal.com.au

```html
<!DOCTYPE html>
<html lang="en">
<head>
<meta charset="utf-8">
<title>Quayvale Legal – Business Card</title>
<link href="https://fonts.googleapis.com/css2?family=Open+Sans:wght@400;600;700&display=swap" rel="stylesheet">
<style>
  :root {
    --navy: #0c1a52;
    --black: #050505;
    --white: #ffffff;
    --bg-light: #ececed;
    --bg-dark: #c6c7c9;
    --ink: #0a0a0a;
  }
  * { margin: 0; padding: 0; box-sizing: border-box; }
  html, body { width: 1200px; height: 1141px; overflow: hidden; }
  body {
    position: relative;
    background: linear-gradient(160deg, var(--bg-light) 0%, var(--bg-dark) 100%);
    font-family: "Open Sans", Arial, sans-serif;
  }
  .card {
    position: absolute;
    overflow: hidden;
    transform-origin: 0 0;
    transform: scale(1.031);
  }
  .card-front {
    left: 83px; top: 101px;
    width: 735px; height: 420px;
    border-radius: 18px;
    background: var(--black);
  }
  .card-back {
    left: 351px; top: 596px;
    width: 733px; height: 419px;
    border-radius: 40px;
    background: var(--black);
  }
  .front-shapes { position: absolute; inset: 0; width: 100%; height: 100%; }

  .brand { position: absolute; text-align: center; font-weight: 400; }
  .brand-mark { display: block; margin: 0 auto; }
  .brand-name { display: block; line-height: 1; }
  .brand-sub { display: block; line-height: 1; }

  .card-front .brand { left: 44px; top: 26px; width: 310px; color: var(--ink); }
  .card-front .brand-mark { width: 70px; height: 70px; background: var(--navy); }
  .card-front .brand-name { margin-top: 56px; font-size: 44px; letter-spacing: 2px; }
  .card-front .brand-sub { margin-top: 12px; font-size: 17px; letter-spacing: 21px; padding-left: 21px; }

  .person { position: absolute; right: 30px; top: 22px; text-align: right; color: var(--white); }
  .person-name { font-size: 27px; font-weight: 700; line-height: 1.2; }
  .person-title { font-size: 20px; font-weight: 400; line-height: 1.4; }

  .address { position: absolute; left: 41px; top: 340px; color: var(--white); font-size: 19.5px; line-height: 30px; }

  .contacts { position: absolute; right: 30px; top: 276px; list-style: none; color: var(--white); font-size: 19.5px; line-height: 33px; text-align: right; }
  .contacts li { display: flex; justify-content: flex-end; align-items: center; gap: 5px; }
  .contacts svg { width: 17px; height: 17px; flex: none; }

  .card-back .brand { left: 0; width: 100%; top: 74px; color: var(--white); }
  .card-back .brand-mark { width: 86px; height: 86px; background: var(--white); }
  .card-back .brand-name { margin-top: 56px; font-size: 54px; letter-spacing: 3px; }
  .card-back .brand-sub { margin-top: 14px; font-size: 20px; letter-spacing: 25px; padding-left: 25px; }
  .back-url { position: absolute; left: 0; width: 100%; top: 350px; text-align: center; color: var(--white); font-size: 22px; letter-spacing: 4px; }
  .back-url strong { font-weight: 700; }
</style>
</head>
<body>

<section class="card card-front">
  <svg class="front-shapes" viewBox="0 0 735 420" preserveAspectRatio="none" aria-hidden="true">
    <path d="M0,196 C80,292 200,318 320,306 C450,292 560,236 735,232 L735,420 L0,420 Z" fill="var(--navy)"/>
    <path d="M0,206 C80,302 200,322 320,310 C450,296 560,248 735,244" fill="none" stroke="var(--white)" stroke-width="3"/>
    <path d="M0,198 C80,294 200,314 320,302 C450,288 560,232 735,226" fill="none" stroke="var(--navy)" stroke-width="2"/>
    <ellipse cx="205" cy="108" rx="240" ry="180" fill="var(--black)"/>
    <ellipse cx="203" cy="104" rx="236" ry="181" fill="none" stroke="var(--navy)" stroke-width="2.5"/>
    <ellipse cx="200" cy="104" rx="230" ry="180" fill="var(--white)"/>
  </svg>

  <div class="brand">
    <span class="brand-mark"></span>
    <span class="brand-name">QUAYVALE</span>
    <span class="brand-sub">LEGAL</span>
  </div>

  <div class="person">
    <p class="person-name">Paul Whitcombe</p>
    <p class="person-title">Managing Partner</p>
  </div>

  <address class="address" style="font-style: normal;">
    Level 9, 7 Ferris Lane<br>
    Sydney NSW 2000
  </address>

  <ul class="contacts">
    <li>
      <svg viewBox="0 0 20 20" aria-hidden="true"><circle cx="10" cy="10" r="8.5" fill="none" stroke="currentColor" stroke-width="1.6"/><path d="M7 5.5 L9 8 L8 9.3 C8.6 10.6 9.4 11.4 10.7 12 L12 11 L14.5 13 L13.2 14.6 C9.6 14.2 5.8 10.4 5.4 6.8 Z" fill="currentColor"/></svg>
      02 9364 2710(Main)
    </li>
    <li>
      <svg viewBox="0 0 20 20" aria-hidden="true"><circle cx="10" cy="10" r="8.5" fill="none" stroke="currentColor" stroke-width="1.6"/><path d="M7 5.5 L9 8 L8 9.3 C8.6 10.6 9.4 11.4 10.7 12 L12 11 L14.5 13 L13.2 14.6 C9.6 14.2 5.8 10.4 5.4 6.8 Z" fill="currentColor"/></svg>
      02 8472 3159(Direct)
    </li>
    <li>
      <svg viewBox="0 0 20 20" aria-hidden="true"><rect x="2" y="5" width="16" height="11" fill="currentColor"/><path d="M2 5 L10 11 L18 5" fill="none" stroke="var(--navy)" stroke-width="1.6"/></svg>
      paul@qvlegal.com.au
    </li>
    <li>
      <svg viewBox="0 0 20 20" aria-hidden="true" fill="none" stroke="currentColor" stroke-width="1.4"><circle cx="10" cy="10" r="8"/><ellipse cx="10" cy="10" rx="3.5" ry="8"/><path d="M2 10 H18 M3.5 6 H16.5 M3.5 14 H16.5"/></svg>
      www.qvlegal.com.au
    </li>
  </ul>
</section>

<section class="card card-back">
  <div class="brand">
    <span class="brand-mark"></span>
    <span class="brand-name">QUAYVALE</span>
    <span class="brand-sub">LEGAL</span>
  </div>
  <p class="back-url">www.<strong>qvlegal</strong>.com.au</p>
</section>

</body>
</html>
```